Casino with the 'highest winning percentage' needs a stationery design

This is for a casino in Colombo, Sri Lanka and we need a stationery design for business card, letter head and envelope.

Should be very professional, simple and elegant without fancy fonts

Reason: Not fully satisfied with the designs. Need more designs.

Business

• 1. card deck symbol 'CLUBS' in red, or black

2. name in BLOCK CAPITAL LETTERS

3. Preferred font colours are black, white or red

4. Prefer 'professional /elegant' fonts
• SHOULD NOT HAVE ANY OTHER SYMBOL EXCEPT 'CLUBS'

DO NOT PREFER ITALIC FONTS

```html
<!DOCTYPE html>
<html lang="en">
<head>
<meta charset="utf-8">
<title>Corvan Entertainment – Business Card</title>
<link rel="stylesheet" href="https://fonts.googleapis.com/css2?family=Noto+Serif:wght@400;700&display=swap">
<style>
  :root {
    --backdrop: #e9e5df;
    --card: #ffffff;
    --card-edge: #cfcac3;
    --ink: #111111;
    --body: #333333;
    --red: #d42e44;
    --rule: #c9c9c9;
    --icon: #c8283d;
  }
  * { margin: 0; padding: 0; box-sizing: border-box; }
  html, body { width: 1200px; height: 372px; overflow: hidden; }
  body {
    background: var(--backdrop);
    font-family: "Noto Serif", Georgia, serif;
    color: var(--ink);
    position: relative;
  }
  .card {
    position: absolute;
    top: 31px;
    width: 556px;
    height: 317px;
    background: var(--card);
    border: 1px solid var(--card-edge);
    overflow: hidden;
  }
  .card--front { left: 36px; }
  .card--back { left: 620px; width: 558px; }

  .brand-mark {
    position: absolute;
    border-radius: 50%;
    background: var(--red);
  }
  .brand-name {
    position: absolute;
    font-weight: 700;
    color: var(--ink);
    line-height: 1.34;
    letter-spacing: 0.3px;
  }
  .card--front .brand-mark { left: 110px; top: 40px; width: 70px; height: 70px; }
  .card--front .brand-name { left: 212px; top: 40px; font-size: 27px; }
  .card--back .brand-mark { left: 88px; top: 126px; width: 76px; height: 76px; }
  .card--back .brand-name { left: 196px; top: 124px; font-size: 30px; }

  .company {
    position: absolute;
    right: 289px;
    top: 166px;
    text-align: right;
  }
  .company__name {
    font-size: 17px;
    font-weight: 700;
    color: var(--red);
    letter-spacing: 0.4px;
  }
  .company__address {
    margin-top: 10px;
    font-style: normal;
    font-size: 13.5px;
    line-height: 19px;
    color: var(--body);
  }
  .divider {
    position: absolute;
    left: 283px;
    top: 157px;
    width: 1px;
    height: 114px;
    background: var(--rule);
  }
  .contacts {
    position: absolute;
    left: 302px;
    top: 162px;
    list-style: none;
  }
  .contacts li {
    display: flex;
    align-items: center;
    height: 20.75px;
    font-size: 13.5px;
    color: var(--body);
  }
  .contacts svg {
    width: 11px;
    height: 11px;
    margin-right: 8px;
    fill: var(--icon);
    flex: none;
  }
  .accent-band {
    position: absolute;
    left: 0;
    bottom: 0;
    width: 556px;
    height: 17px;
  }
  .tagline {
    position: absolute;
    left: 0;
    right: 0;
    top: 243px;
    text-align: center;
    font-size: 17px;
    font-weight: 700;
    color: var(--red);
    letter-spacing: 2px;
  }
</style>
</head>
<body>

<section class="card card--front">
  <span class="brand-mark"></span>
  <div class="brand-name">CORVAN<br>ENTERTAINMENT</div>

  <div class="company">
    <div class="company__name">CORVAN LIMITED</div>
    <address class="company__address">
      18, Harbour Crest Road<br>
      Seaview 01000<br>
      Sri Lanka
    </address>
  </div>

  <span class="divider"></span>

  <ul class="contacts">
    <li>
      <svg viewBox="0 0 12 12"><circle cx="6" cy="6" r="6"/><path d="M3.6 3.2c.4-.4.9-.3 1.1.1l.5 1c.2.3 0 .6-.2.8l-.3.3c.3.8.9 1.4 1.7 1.8l.3-.3c.2-.2.5-.3.8-.2l1 .5c.4.2.5.7.1 1.1-.7.8-1.8.7-3.2-.4C4 6.9 3.1 5.7 3 4.7c0-.6.2-1.1.6-1.5z" fill="#fff"/></svg>
      + 94 11 5550142
    </li>
    <li>
      <svg viewBox="0 0 12 12"><rect x="3" y="0.5" width="6" height="11" rx="1"/><rect x="4" y="2" width="4" height="5" fill="#fff"/><circle cx="6" cy="9.3" r="0.8" fill="#fff"/></svg>
      + 94 77 0000000
    </li>
    <li>
      <svg viewBox="0 0 12 12"><path d="M2.5 5l1.2-2.6c.2-.4.5-.6.9-.6h2.8c.4 0 .7.2.9.6L9.5 5H11v4H1V5z"/><circle cx="3.2" cy="9.6" r="1.3"/><circle cx="8.8" cy="9.6" r="1.3"/><rect x="3.8" y="2.8" width="4.4" height="2" fill="#fff"/></svg>
      + 94 11 0000000
    </li>
    <li>
      <svg viewBox="0 0 12 12"><rect x="0.5" y="2" width="11" height="8" rx="1"/><path d="M1.5 3l4.5 3.5L10.5 3" fill="none" stroke="#fff" stroke-width="1.2"/></svg>
      info@corvanplay.com
    </li>
    <li>
      <svg viewBox="0 0 12 12"><circle cx="6" cy="6" r="5.5"/><g fill="none" stroke="#fff" stroke-width="0.8"><ellipse cx="6" cy="6" rx="2.2" ry="5"/><path d="M1 6h10M1.8 3.5h8.4M1.8 8.5h8.4"/></g></svg>
      www.corvanplay.com
    </li>
  </ul>

  <svg class="accent-band" viewBox="0 0 556 17" preserveAspectRatio="none" aria-hidden="true">
    <polygon points="0,0 294,0 277,17 0,17" fill="#111111"/>
    <polygon points="318,0 556,0 556,17 301,17" fill="#d42e44"/>
  </svg>
</section>

<section class="card card--back">
  <span class="brand-mark"></span>
  <div class="brand-name">CORVAN<br>ENTERTAINMENT</div>
  <p class="tagline">Highest Winning Percentage In The World</p>
</section>

</body>
</html>
```